Web Design Project

Hi, we need a new and professional design for our company "partnertradecircuitry". The website should communicate business but with a friendly and professional touch.

You can use the following categories for the menu;

Home - customer groups - products - voucher system- contact

Give it your best,

Regards,
Oswin

Industry/Entity Type

Business

```html
<!DOCTYPE html>
<html lang="en">
<head>
<meta charset="utf-8">
<title>partnertradecircuitry</title>
<link href="https://fonts.googleapis.com/css2?family=PT+Sans:wght@400;700&family=Roboto+Condensed:wght@400;700&display=swap" rel="stylesheet">
<style>
:root{
  --page:#e4e1d8;
  --panel:#ffffff;
  --ink:#3a3a3a;
  --muted:#7a7a7a;
  --text:#454545;
  --link:#1a5fb4;
  --blue:#0b64c8;
  --blue-dark:#0a4fa0;
  --date-blue:#2a86d0;
  --nav:#f1efe9;
  --nav-edge:#d9d5ca;
  --contact:#c8c09e;
  --rule:#b9b9b9;
}
*{margin:0;padding:0;box-sizing:border-box}
html,body{width:1200px;height:1128px;overflow:hidden}
body{background:var(--page);font-family:"PT Sans",sans-serif;color:var(--text);position:relative}
.abs{position:absolute}
.datetime{left:86px;top:70px;font-size:15px;color:#555}
.datetime b{font-weight:700}
.datetime .time{margin-left:16px;font-weight:700}
.panel{left:345px;top:36px;width:836px;height:1020px;background:var(--panel);border-radius:10px;box-shadow:0 3px 8px rgba(0,0,0,.15)}
.toolbar{left:394px;top:66px;display:flex;align-items:center}
.toolbar svg{display:block}
.toolbar .sep{width:1px;height:26px;background:#d0d0d0;margin:0 36px}
.header{left:19px;top:114px;width:1162px;height:188px;background:linear-gradient(180deg,#f0dcb8,#e3c391 55%,#cfa86e);box-shadow:0 3px 6px rgba(0,0,0,.2)}
.header-photo{left:345px;top:114px;width:391px;height:188px;background:radial-gradient(circle at 55% 45%,#7fbf4a 0,#3f8a2a 35%,#d9b48a 60%,#e8cfa8 100%)}
.logo{left:40px;top:186px;font-family:"PT Sans",sans-serif;font-weight:700;font-size:30px;color:#1e8ed8;letter-spacing:-.3px}
.banner{left:736px;top:154px;width:445px;height:104px;background:linear-gradient(180deg,var(--blue),var(--blue-dark));border-radius:4px 0 0 4px;box-shadow:inset 0 0 0 2px rgba(255,255,255,.5);color:#fff;font-family:"Roboto Condensed",sans-serif;padding:18px 0 0 26px}
.banner .big{font-size:42px;line-height:42px;letter-spacing:.5px}
.banner .small{font-size:23px;line-height:28px}
.banner-dot{left:1125px;top:139px;width:32px;height:32px;border-radius:50%;background:#fff;box-shadow:0 1px 3px rgba(0,0,0,.4)}
.nav{left:34px;top:312px;width:309px}
.nav a{display:block;height:78px;margin-bottom:10px;background:linear-gradient(180deg,#f7f6f2,var(--nav));border:1px solid var(--nav-edge);border-right:none;border-radius:5px 0 0 5px;padding:14px 0 0 31px;text-decoration:none;box-shadow:0 2px 3px rgba(0,0,0,.08)}
.nav .t{display:block;font-family:"Roboto Condensed",sans-serif;font-size:22px;color:var(--ink);line-height:24px}
.nav .s{display:block;font-size:15px;color:var(--muted);line-height:16px}
.contact{left:34px;top:849px;width:311px;height:157px;background:var(--contact);border-radius:6px 0 0 6px;padding:14px 0 0 46px;color:#4d4a3d;font-size:16px;line-height:21px}
.contact h3{font-family:"Roboto Condensed",sans-serif;font-weight:400;font-size:27px;color:#55523f;line-height:32px;margin-bottom:6px}
.ph{background:linear-gradient(135deg,#d9dde2,#b7c2cc)}
h2{font-family:"Roboto Condensed",sans-serif;font-weight:700;font-size:31px;color:var(--ink);letter-spacing:-.5px;line-height:32px}
.sub{font-family:"Roboto Condensed",sans-serif;font-size:18px;color:var(--muted);line-height:20px}
p{font-size:15.5px;line-height:20.5px;color:var(--text)}
.more{font-size:16px;color:var(--link)}
.more::before{content:"|  ";color:#aaa}
.more::after{content:"|";color:#aaa}
.rule{height:1px;background:var(--rule)}
.list{list-style:none}
.list li{font-size:16px;color:var(--link);height:28px;line-height:26px;border-bottom:1px dotted #b5b5b5;padding-left:30px;position:relative}
.list li::before{content:"";position:absolute;left:14px;top:12px;width:5px;height:5px;border:1px solid #999;border-radius:50%}
.date{font-size:21px;font-weight:700;color:var(--date-blue)}
.footer{left:0;width:1200px;top:1071px;text-align:center;font-size:16px;color:#555}
</style>
</head>
<body>
<div class="abs datetime"><b>FRI</b> 00.00.2013 <span class="time">5:45 PM</span></div>

<div class="abs panel"></div>

<div class="abs toolbar">
  <svg width="24" height="24" viewBox="0 0 24 24" aria-label="Home"><path d="M4 12 12 5l8 7M7 10v8h10v-8" fill="none" stroke="#777" stroke-width="1.6"/></svg>
  <span class="sep"></span>
  <svg width="24" height="24" viewBox="0 0 24 24" aria-label="Page"><path d="M8 5h6l3 3v11H8z" fill="none" stroke="#777" stroke-width="1.6"/></svg>
  <span class="sep"></span>
  <svg width="24" height="24" viewBox="0 0 24 24" aria-label="Sitemap"><path d="M9 5h6v5H9zM4 15h5v4H4zM15 15h5v4h-5zM12 10v3M6.5 13h11v2M6.5 13v2" fill="none" stroke="#777" stroke-width="1.6"/></svg>
</div>

<div class="abs header"></div>
<div class="abs header-photo" role="img" aria-label="Photo of hands holding a green globe"></div>
<div class="abs logo">partnertradecircuitry</div>
<div class="abs banner"><div class="big">INDIVIDUAL</div><div class="small">CUSTOMERS APPROACH</div></div>
<div class="abs banner-dot"></div>

<nav class="abs nav">
  <a href="#"><span class="t">Home</span><span class="s">lorem empus</span></a>
  <a href="#"><span class="t">Customer Groups</span><span class="s">lorem epsum</span></a>
  <a href="#"><span class="t">Products</span><span class="s">lorum epsum</span></a>
  <a href="#"><span class="t">Voucher System</span><span class="s">lerum epsum</span></a>
  <a href="#"><span class="t">Contact</span><span class="s">lerum epsum</span></a>
</nav>

<div class="abs contact">
  <h3>Primary Contact</h3>
  <b>The Company Name Inc.</b><br>
  4120 - 4124 Alder Lane,<br>
  Brookfield, KT04 7RP<br>
  <b>Phone:</b>&nbsp; +1 800 555 0142
</div>

<div class="abs ph" style="left:381px;top:400px;width:222px;height:183px;background:radial-gradient(circle,#8aa3b8 0,#5c7890 55%,#ffffff 72%)" role="img" aria-label="Illustration of connected people in a network"></div>

<div class="abs" style="left:631px;top:378px;width:500px">
  <h2>Welcome to our Company Website</h2>
  <div class="sub">Some words about company</div>
  <p style="margin-top:22px">Donec et tortor. Praesent iaculis vestibulum neque arcu tortor... fringilla ut, suscipit ac, condimentum sit amet, est. Praesent malesuada purus at dolor. Maecenas porttitor, ante nec pulvinar suscipit, ante nisl lobortis dui, eu malesuada pede tortor mollis wisi. Suspendisse egestas. Quisque enim...</p>
  <div class="more" style="text-align:right;margin-top:8px">read more about company</div>
</div>

<div class="abs" style="left:393px;top:630px;width:336px">
  <h2>Priority line of business</h2>
  <div class="sub">Professional management and researches</div>
  <div class="rule" style="margin-top:10px"></div>
  <p style="margin-top:26px">Praesent malesuada purus at dolor. Suspendisse egestas. Quisque enim. Duis neque pede, ultrices sed, vulputate at, vestibulum id, nunc quisque orci quam, consectetuer quis, rhoncus sed...</p>
  <ul class="list" style="margin-top:14px">
    <li>Praesent malesuada purus at dolor.</li>
    <li>Suspendisse egestas quisque enim.</li>
    <li>Duis neque pede ultrices sed vulput</li>
    <li>Quisque orci quam, consectetuer quis</li>
    <li>Rhoncus sed vehicula nec velit.</li>
  </ul>
</div>

<div class="abs" style="left:762px;top:616px;width:1px;height:366px;background:var(--rule)"></div>

<div class="abs" style="left:794px;top:630px;width:337px">
  <h2>Latest News</h2>
  <div class="sub">corporate highlights</div>
  <div class="rule" style="margin-top:10px"></div>
</div>

<div class="abs ph" style="left:788px;top:710px;width:140px;height:136px;border-radius:50%;background:radial-gradient(circle at 40% 35%,#ffffff,#dcdcdc 70%,#c4c4c4)" role="img" aria-label="Illustration of a cloud labelled network"></div>
<div class="abs" style="left:945px;top:722px;width:186px">
  <p><span class="date">21.05</span>&nbsp; Praesent iaculis vestibulum neque arcu tortor fringilla ut, suscipit ac, condimentum sit...</p>
  <div class="more" style="text-align:right;margin-top:6px">read more</div>
</div>

<div class="abs" style="left:794px;top:866px;width:337px;border-top:1px dotted #b5b5b5"></div>

<div class="abs ph" style="left:812px;top:877px;width:101px;height:102px;border-radius:50%;background:radial-gradient(circle at 40% 35%,#c8d4f0,#4a5e96 55%,#1f2b55)" role="img" aria-label="Illustration of a glass sphere with network lines"></div>
<div class="abs" style="left:945px;top:878px;width:186px">
  <p><span class="date">15.05</span>&nbsp; Praesent male-suada purus at dolor. Maecenas porttitor, ante nec pulvinar suscipit...</p>
  <div class="more" style="text-align:right;margin-top:6px">read more</div>
</div>

<div class="abs footer">partnertradecircuitry.Com © 2013 | Privacy Policy | Terms Of Use</div>
</body>
</html>
```